Veltrane Group Business Card Design

The CEO is looking for a new trendy look for his business card.
You can stay with current branding or come up with something new/creative. It can be 3D, including Medical Office buildings. You can use our logo in a variety of colors. Please include name, title, company name, company website, email address, cell number

Target Market(s)

Real Estate Development and Construction

Industry/Entity Type

Health care real estate

Contact Information for Business Card

Rohesh Kamdar, CEO M-604.781.2249 E-roheshkamdar@veltrane.com Address:4180 Lindqvist Ave, Tampa, FL 33482 www.veltrane.com

Font styles to use
Other font styles liked:
• Be creative

Requirements
Must have
• Creative, trendy look
Nice to have
• Please go to our website to get a feel- www. veltrane.com
Should not have
• small fonts

```html
<!DOCTYPE html>
<html lang="en">
<head>
<meta charset="utf-8">
<title>Veltrane Group Business Card</title>
<link href="https://fonts.googleapis.com/css2?family=Archivo:wght@400;800&display=swap" rel="stylesheet">
<style>
  :root {
    --brand-red: #b0222d;
    --brand-red-soft: #b72a33;
    --brand-navy: #1e2f52;
    --paper: #ffffff;
    --ink: #222833;
    --rule: #5a6478;
    --stage: #d3d3d3;
  }
  * { margin: 0; padding: 0; box-sizing: border-box; }
  html, body { width: 1200px; height: 788px; overflow: hidden; }
  body {
    background: var(--stage);
    font-family: "Archivo", Arial, sans-serif;
    display: flex;
    align-items: center;
    justify-content: center;
    gap: 40px;
  }
  .card {
    position: relative;
    width: 540px;
    height: 309px;
    border-radius: 18px;
    overflow: hidden;
    box-shadow: 0 6px 18px rgba(0,0,0,0.18);
  }
  .card-front { background: var(--paper); }
  .front-wave { position: absolute; inset: 0; width: 100%; height: 100%; }
  .wordmark {
    position: absolute;
    left: 34px;
    top: 108px;
    width: 210px;
    font-weight: 800;
    font-size: 40px;
    line-height: 0.98;
    letter-spacing: -1px;
    color: var(--brand-red);
  }
  .wordmark span { display: block; }
  .divider {
    position: absolute;
    left: 258px;
    top: 48px;
    width: 1px;
    height: 150px;
    background: var(--rule);
  }
  .contact {
    position: absolute;
    left: 276px;
    top: 42px;
    width: 250px;
    color: var(--ink);
    font-size: 13px;
    line-height: 1.35;
  }
  .contact-name {
    font-weight: 800;
    font-size: 20px;
    color: var(--brand-red);
    letter-spacing: 0.3px;
    line-height: 1.1;
    white-space: nowrap;
  }
  .contact-title { margin-bottom: 8px; }
  .contact-address { margin-bottom: 6px; }
  .contact-line { display: flex; align-items: center; gap: 6px; white-space: nowrap; }
  .contact-line svg { width: 10px; height: 10px; flex: none; }
  .card-back {
    background: var(--brand-red-soft);
    display: flex;
    align-items: center;
    justify-content: center;
  }
  .wordmark-reverse {
    font-weight: 800;
    font-size: 54px;
    line-height: 0.98;
    letter-spacing: -1px;
    color: var(--paper);
  }
  .wordmark-reverse span { display: block; }
</style>
</head>
<body>
  <section class="card card-front" aria-label="Card front">
    <svg class="front-wave" viewBox="0 0 540 309" preserveAspectRatio="none" aria-hidden="true">
      <path d="M0 236 C 180 236, 400 200, 540 282 L540 309 L0 309 Z" fill="var(--brand-navy)"/>
      <path d="M0 242 C 180 242, 400 208, 540 290 L540 309 L0 309 Z" fill="var(--brand-red)"/>
    </svg>
    <div class="wordmark"><span>Veltrane</span><span>Group</span></div>
    <div class="divider"></div>
    <div class="contact">
      <div class="contact-name">ROHESH KAMDAR</div>
      <div class="contact-title">CEO</div>
      <div class="contact-address">4180 Lindqvist Ave, Tampa<br>FL 33482</div>
      <div class="contact-line">
        <svg viewBox="0 0 10 10"><path d="M2 1 L4 1 L4.6 3 L3.4 3.8 Q4.4 5.8 6.2 6.6 L7 5.4 L9 6 L9 8 Q9 9 8 9 Q1 8.4 1 2 Q1 1 2 1Z" fill="var(--brand-red)"/></svg>
        <span>604.781.2249</span>
      </div>
      <div class="contact-line">
        <svg viewBox="0 0 10 10"><rect x="0.5" y="2" width="9" height="6.5" fill="var(--brand-red)"/><path d="M0.5 2 L5 5.5 L9.5 2" stroke="#fff" stroke-width="0.9" fill="none"/></svg>
        <span>roheshkamdar@veltrane.com</span>
      </div>
      <div class="contact-line">
        <svg viewBox="0 0 10 10"><circle cx="5" cy="5" r="4.5" fill="var(--brand-red)"/><path d="M0.5 5 H9.5 M5 0.5 Q2.5 5 5 9.5 M5 0.5 Q7.5 5 5 9.5" stroke="#fff" stroke-width="0.7" fill="none"/></svg>
        <span>www.veltrane.com</span>
      </div>
    </div>
  </section>

  <section class="card card-back" aria-label="Card back">
    <div class="wordmark-reverse"><span>Veltrane</span><span>Group</span></div>
  </section>
</body>
</html>
```